Fenwick Grading LTD - website for irrigation & Landscape Lighting & Buried service wire

Looking for a website to help promote my business with Irrigation (installation, service, etc) and buried service wire/drainage solutions.

Commercial/Residential

Landscape lighting.

I’ll get photos in the trucks and trailers to upload as well maybe the machine as well.

Target Market(s)

Homeowners who want green grass and beautiful gardens. Beautiful landscape lighting

Industry/Entity Type

Irrigation systems and landscape lighting and buried service wire to homes and offering Drainage soltions.

Coding

Coded - Design and coding required

Number of Pages Required

4 page

Colors
F0912C
F2A743
F7CA91
FBE8D2
FDF5EE

Requirements
Must have
• was hoping to link up my email on fenwickgrading@mailbox-example.net with the website if possible.
Nice to have
• Page for Irrigation, page for landscape lighting, page buried service wire & drainage soltions.

```html
<!DOCTYPE html>
<html lang="en">
<head>
<meta charset="utf-8">
<title>Fenwick Grading LTD</title>
<link href="https://fonts.googleapis.com/css2?family=Lato:wght@400;700;900&family=Roboto:wght@400;500;700&display=swap" rel="stylesheet">
<style>
:root{
  --orange:#ea8418;
  --orange-soft:#f2a743;
  --orange-pale:#f7ca91;
  --cream:#fdf5ee;
  --grey:#888888;
  --grey-light:#efefef;
  --grey-band:#efeded;
  --ink:#111111;
  --text:#555555;
  --white:#ffffff;
  --black:#0b0b0b;
}
*{margin:0;padding:0;box-sizing:border-box}
html,body{width:1200px;height:3903px;overflow:hidden}
body{position:relative;background:var(--white);font-family:'Roboto',Arial,sans-serif;color:var(--ink)}
.abs{position:absolute}
.heading{font-family:'Lato',Arial,sans-serif;font-weight:400;font-size:43px;letter-spacing:.5px;text-align:center;color:var(--ink)}
.heading b{color:var(--orange);font-weight:900}
.heading-bar{width:98px;height:8px;background:var(--ink);margin:10px auto 0;clip-path:polygon(0 0,100% 0,88% 100%,12% 100%)}

/* header */
.site-header{top:0;left:0;width:1200px;height:96px;background:var(--white);box-shadow:0 2px 6px rgba(0,0,0,.08);z-index:5}
.brand{left:110px;top:16px;display:flex;align-items:center;gap:8px}
.brand-square{width:14px;height:14px;background:var(--orange)}
.brand-name{font-family:'Lato',sans-serif;font-weight:900;color:var(--orange);font-size:17px;line-height:20px;letter-spacing:.5px}
.topbar{left:594px;top:0;width:606px;height:33px;background:var(--orange);display:flex;align-items:center;color:var(--white);font-size:14px}
.topbar span{display:flex;align-items:center;gap:7px;padding:0 22px;height:100%;border-left:2px solid rgba(255,255,255,.6);transform:skewX(-18deg)}
.topbar span>*{transform:skewX(18deg)}
.topbar span:first-child{border-left:none}
.social-dot{width:14px;height:14px;background:var(--white);border-radius:2px}
.nav{left:455px;top:59px;display:flex;gap:37px;font-size:14px;color:#333}

/* hero */
.hero{top:96px;left:0;width:1200px;height:677px}
.hero-copy{left:113px;top:144px;color:var(--white)}
.hero-welcome{font-size:17px;font-weight:500}
.hero-title{font-family:'Lato',sans-serif;font-weight:900;font-size:57px;line-height:1;margin-top:24px}
.hero-sub{font-family:'Lato',sans-serif;font-weight:900;font-size:31px;margin-top:8px}
.hero-text{font-size:15px;line-height:23px;margin-top:20px;width:290px}
.btn-pair{display:flex;height:44px;margin-top:33px}
.btn{display:flex;align-items:center;justify-content:center;font-weight:700;font-size:18px;color:var(--white);width:158px}
.btn-primary{background:var(--orange);clip-path:polygon(0 0,92% 0,100% 100%,0 100%);width:160px}
.btn-secondary{background:var(--grey);margin-left:-8px;clip-path:polygon(0 0,100% 0,100% 100%,8% 100%);width:155px;padding-left:12px;padding-bottom:8px}
.btn-light{background:var(--white);color:var(--ink)}

/* services */
.services{top:773px;left:0;width:1200px;height:783px}
.services .heading{position:absolute;top:78px;width:1200px}
.diamond{position:absolute;transform:rotate(45deg)}
.diamond .fill{position:absolute;inset:0}
.badge{position:absolute;width:54px;height:54px;background:var(--white);transform:rotate(45deg);box-shadow:0 2px 6px rgba(0,0,0,.15)}
.badge i{position:absolute;left:19px;top:19px;width:16px;height:16px;background:var(--orange);border-radius:50%;transform:rotate(-45deg)}
.service-label{position:absolute;font-family:'Lato',sans-serif;font-weight:700;font-size:18px;text-align:center;width:300px}

/* work */
.work{top:1556px;left:0;width:1200px;height:565px;background:var(--orange);overflow:hidden}
.work-copy{left:110px;top:72px;color:var(--white)}
.work-copy .heading{color:var(--white);text-align:left}
.work-copy .heading b{color:var(--white)}
.work-copy .heading-bar{background:var(--white);margin:8px 0 0}
.work-type{font-size:29px;margin-top:42px;font-weight:500}
.work-text{font-size:14px;line-height:23px;width:380px;text-align:justify;margin-top:18px;padding-left:4px}

/* testimonials */
.testimonials{top:2121px;left:0;width:1200px;height:538px}
.testimonials .heading{position:absolute;top:78px;width:1200px}
.card{position:absolute;top:185px;width:362px;height:224px;background:var(--white);box-shadow:0 3px 14px rgba(0,0,0,.14)}
.card-text{position:absolute;left:49px;top:24px;width:272px;font-size:13.5px;line-height:23px;color:var(--text)}
.card-more{position:absolute;left:232px;top:119px;font-size:12px;text-decoration:underline;color:#222}
.card-name{position:absolute;left:110px;top:155px;font-size:19px;font-weight:500}
.card-stars{position:absolute;left:242px;top:157px;color:#f05a22;font-size:16px;letter-spacing:2px}
.card-role{position:absolute;left:110px;top:190px;font-size:13px;color:var(--text)}
.avatar{position:absolute;width:122px;height:122px;transform:rotate(45deg);border:5px solid var(--orange);border-left-color:#fff;border-top-color:#fff}
.arrow{position:absolute;width:30px;height:30px;background:#e8e8e8;transform:rotate(45deg);display:flex;align-items:center;justify-content:center}
.arrow svg{transform:rotate(-45deg)}

/* benefits band */
.band{top:2659px;left:0;width:1200px;height:359px;background:var(--grey-band);overflow:hidden}
.band-list{left:770px;top:90px;font-size:21px;font-weight:500;letter-spacing:.3px}
.band-list li{list-style:none;display:flex;align-items:center;gap:10px;height:46px;white-space:nowrap}
.band-end{font-size:26px;font-weight:400;margin-top:6px;letter-spacing:.3px}

/* audience */
.audience{top:3018px;left:0;width:1200px;height:517px;overflow:hidden}
.audience-copy{left:113px;top:172px;font-size:22px;line-height:32px;color:var(--ink);width:345px}
.audience-copy p+p{margin-top:30px}

/* footer */
.footer{top:3535px;left:0;width:1200px;height:368px;background:var(--black);color:var(--white)}
.footer-brand{left:114px;top:78px;display:flex;align-items:center;gap:8px}
.footer-brand .brand-name{color:var(--white)}
.footer-about{left:115px;top:160px;font-size:14px;line-height:23px}
.footer-col{top:148px;font-size:14px;line-height:23px}
.footer-col h4{font-size:17px;font-weight:500;margin-bottom:14px}
.footer-mail{left:896px;top:152px;font-size:14px;line-height:23px;width:290px}
.footer-mail a{color:var(--orange-soft);text-decoration:underline}
.footer-rule{left:380px;top:298px;width:520px;height:1px;background:#222}
.copyright{left:0;top:313px;width:1200px;text-align:center;font-size:12px}
.footer-social{left:1036px;top:300px;width:40px;height:40px;border-radius:50%;background:#333}
</style>
</head>
<body>

<header class="site-header abs">
  <div class="brand abs"><div class="brand-square"></div><div class="brand-name">FENWICK<br>GRADING LTD</div></div>
  <div class="topbar abs">
    <span><i class="social-dot"></i></span>
    <span><b style="display:flex;gap:7px;font-weight:400"><svg width="13" height="13" viewBox="0 0 24 24"><path fill="#fff" d="M6.6 10.8a15 15 0 0 0 6.6 6.6l2.2-2.2a1 1 0 0 1 1-.25 11.4 11.4 0 0 0 3.6.57 1 1 0 0 1 1 1V20a1 1 0 0 1-1 1A17 17 0 0 1 3 4a1 1 0 0 1 1-1h3.5a1 1 0 0 1 1 1c0 1.25.2 2.45.57 3.57a1 1 0 0 1-.25 1z"/></svg>+1 (555) 0142 300</b></span>
    <span><b style="display:flex;gap:7px;font-weight:400"><svg width="14" height="12" viewBox="0 0 24 20"><path fill="#fff" d="M2 0h20a2 2 0 0 1 2 2v1L12 11 0 3V2a2 2 0 0 1 2-2zm-2 6 12 8 12-8v12a2 2 0 0 1-2 2H2a2 2 0 0 1-2-2z"/></svg>fenwickgrading@mailbox-example.net</b></span>
  </div>
  <nav class="nav abs"><span>Home</span><span>Landscape Lighting</span><span>Wire &amp; Drainage</span><span>Irrigation Installs</span><span>Contact</span></nav>
</header>

<section class="hero abs">
  <svg class="abs" width="1200" height="677" viewBox="0 0 1200 677" style="left:0;top:0">
    <defs>
      <linearGradient id="heroFill" x1="0" y1="0" x2="1" y2="1">
        <stop offset="0" stop-color="#5f7a2c"/><stop offset=".45" stop-color="#3e5a1c"/><stop offset="1" stop-color="#6f9a2a"/>
      </linearGradient>
    </defs>
    <polygon points="0,520 600,662 1200,520 1200,540 600,677 0,535" fill="#ea8418"/>
    <polygon role="img" aria-label="Father and child watering a green garden lawn with a hose" points="0,0 1200,0 1200,520 600,662 0,520" fill="url(#heroFill)"/>
  </svg>
  <div class="hero-copy abs">
    <div class="hero-welcome">Welcome To</div>
    <div class="hero-title">FENWICK</div>
    <div class="hero-sub">GRADING LTD</div>
    <p class="hero-text">Lorem ipsum dolor sit amet, consectetur adipiscing elit, sed do eiusmod</p>
    <div class="btn-pair"><span class="btn btn-primary">Residential</span><span class="btn btn-secondary">Commercial</span></div>
  </div>
</section>

<section class="services abs">
  <svg class="abs" width="1200" height="783" style="left:0;top:0"><polygon points="600,0 1200,600 1200,783 0,783 0,600" fill="#efefef"/></svg>
  <h2 class="heading"><b>OUR</b> SERVICES</h2>
  <div class="heading-bar abs" style="left:551px;top:126px"></div>

  <div class="diamond" style="left:168px;top:300px;width:248px;height:248px;background:#7a7a7a">
    <div class="fill" role="img" aria-label="Open trench with buried service wire conduit and drainage pipe being laid" style="inset:14px;background:linear-gradient(135deg,#c69a66,#8a5a34 55%,#3d6fa6)"></div>
  </div>
  <div class="diamond" style="left:783px;top:300px;width:248px;height:248px;background:#7a7a7a">
    <div class="fill" role="img" aria-label="Outdoor patio lounge lit by warm landscape lighting at dusk" style="inset:14px;background:linear-gradient(135deg,#2b241e,#6d4a2c 55%,#1b1a18)"></div>
  </div>
  <div class="diamond" style="left:447px;top:269px;width:306px;height:306px;background:var(--orange)">
    <div class="fill" role="img" aria-label="Mother and child watering garden plants with a hose" style="inset:14px;background:linear-gradient(135deg,#d8b98a,#6f7f3a 55%,#3c4c22)"></div>
  </div>
  <div class="badge" style="left:222px;top:492px"><i></i></div>
  <div class="badge" style="left:528px;top:525px"><i></i></div>
  <div class="badge" style="left:915px;top:492px"><i></i></div>

  <div class="service-label" style="left:143px;top:638px">Buried Wire &amp; Drainage</div>
  <div class="service-label" style="left:450px;top:671px">Irrigation Installs</div>
  <div class="service-label" style="left:758px;top:638px">Landscape Lighting</div>
</section>

<section class="work abs">
  <svg class="abs" width="1200" height="565" style="left:0;top:0">
    <defs><linearGradient id="workFill" x1="0" y1="0" x2="0" y2="1"><stop offset="0" stop-color="#8cc0ec"/><stop offset=".45" stop-color="#7a9a4a"/><stop offset="1" stop-color="#3f8a1e"/></linearGradient></defs>
    <polygon points="650,0 712,0 575,265 712,565 650,565 530,265" fill="#f2a743" opacity=".55"/>
    <polygon role="img" aria-label="Large house with a freshly mowed green lawn and a person walking across it" points="712,0 1200,0 1200,565 712,565 575,265" fill="url(#workFill)"/>
  </svg>
  <div class="work-copy abs">
    <h2 class="heading"><b>OUR</b> WORK</h2>
    <div class="heading-bar" style="width:98px"></div>
    <div class="work-type">Residential</div>
    <p class="work-text">Lorem ipsum dolor sit amet, consectetur adipiscing elit, sed do eiusmod tempor incididunt ut labore et dolore magna aliqua. Ut enim ad minim veniam, quis nostrud exercitation ullamco laboris nisi ut aliquip ex ea commodo consequat. Duis aute irure dolor in reprehenderit in voluptate velit esse cillum</p>
    <div class="btn-pair" style="margin-top:34px"><span class="btn btn-primary btn-light">Read More</span><span class="btn btn-secondary">Commercial</span></div>
  </div>
</section>

<section class="testimonials abs">
  <svg class="abs" width="1200" height="110" style="left:0;top:0"><polygon points="490,0 710,0 600,100" fill="#efefef"/></svg>
  <h2 class="heading"><b>OUR</b> TESTIMONIALS</h2>
  <div class="heading-bar abs" style="left:551px;top:126px"></div>

  <div class="arrow" style="left:65px;top:281px"><svg width="10" height="10" viewBox="0 0 10 10"><path d="M6.5 1.5 3 5l3.5 3.5" stroke="#333" stroke-width="1.5" fill="none"/></svg></div>
  <div class="arrow" style="left:1104px;top:281px"><svg width="10" height="10" viewBox="0 0 10 10"><path d="M3.5 1.5 7 5 3.5 8.5" stroke="#333" stroke-width="1.5" fill="none"/></svg></div>

  <article class="card" style="left:217px">
    <p class="card-text">Lorem ipsum dolor sit amet, consectetur adipiscing elit, sed do eiusmod tempor incididunt ut labore et dolore magna aliqua. Ut enim ad minim veniam, quis nostrud</p>
    <span class="card-more">Read More</span>
    <div class="card-name">Dara Whitlow</div><div class="card-stars">★★★★★</div>
    <div class="card-role">Lorem ipsum dolor sit amet</div>
  </article>
  <div class="avatar" role="img" aria-label="Portrait of a customer" style="left:145px;top:300px;background:linear-gradient(135deg,#c9c2b8,#8a7a6a)"></div>

  <article class="card" style="left:706px">
    <p class="card-text">Lorem ipsum dolor sit amet, consectetur adipiscing elit, sed do eiusmod tempor incididunt ut labore et dolore magna aliqua. Ut enim ad minim veniam, quis nostrud</p>
    <span class="card-more">Read More</span>
    <div class="card-name">Mira Castell</div><div class="card-stars">★★★★★</div>
    <div class="card-role">Lorem ipsum dolor sit amet</div>
  </article>
  <div class="avatar" role="img" aria-label="Portrait of a customer" style="left:634px;top:300px;background:linear-gradient(135deg,#d9d4cf,#6a5648)"></div>
</section>

<section class="band abs">
  <svg class="abs" width="1200" height="359" style="left:0;top:0">
    <defs><linearGradient id="bandFill" x1="0" y1="0" x2="0" y2="1"><stop offset="0" stop-color="#a8a05a"/><stop offset=".5" stop-color="#5f9a2a"/><stop offset="1" stop-color="#3f7a1a"/></linearGradient></defs>
    <polygon points="605,0 647,0 755,359 713,359" fill="#ea8418"/>
    <polygon role="img" aria-label="Lawn sprinkler spraying water over green grass" points="0,0 605,0 713,359 0,359" fill="url(#bandFill)"/>
  </svg>
  <ul class="band-list abs">
    <li><svg width="22" height="22" viewBox="0 0 24 24"><circle cx="12" cy="12" r="12" fill="#111"/><path d="M6.5 12.5 10.5 16.5 17.5 8.5" stroke="#fff" stroke-width="2.6" fill="none"/></svg>IRRIGATION SYSTEMS</li>
    <li><svg width="22" height="22" viewBox="0 0 24 24"><circle cx="12" cy="12" r="12" fill="#111"/><path d="M6.5 12.5 10.5 16.5 17.5 8.5" stroke="#fff" stroke-width="2.6" fill="none"/></svg>LANDSCAPE LIGHTING</li>
    <li style="margin-top:5px"><svg width="22" height="22" viewBox="0 0 24 24"><circle cx="12" cy="12" r="12" fill="#111"/><path d="M6.5 12.5 10.5 16.5 17.5 8.5" stroke="#fff" stroke-width="2.6" fill="none"/></svg>BURIED WIRE &amp; DRAINAGE</li>
    <li class="band-end">TO HOMES</li>
  </ul>
</section>

<section class="audience abs">
  <div class="abs" role="img" aria-label="Father and young son laughing while spraying water from a garden hose" style="left:0;top:0;width:1200px;height:517px;background:linear-gradient(90deg,#ffffff 0%,#ffffff 38%,#e8eef2 58%,#b9cfe0 78%,#d8a47c 100%)"></div>
  <div class="audience-copy abs">
    <p>Homeowners who want green grass and beautiful gardens.</p>
    <p>Beautiful landscape lighting Irrigation systems and buried service wire and drainage to homes</p>
  </div>
</section>

<footer class="footer abs">
  <div class="footer-brand abs"><div class="brand-square"></div><div class="brand-name">FENWICK<br>GRADING LTD</div></div>
  <div class="footer-about abs">Buried Service Wire &amp; Drainage.<br>Irrigation Systems<br>Professional, clean, take pride in our work.<br>Free Estimates<br>Experienced</div>
  <div class="footer-col abs" style="left:501px"><h4>Quick Links</h4>Home<br>About Us<br>Services<br>Contact Us</div>
  <div class="footer-col abs" style="left:688px"><h4>Location</h4>Lorum Ip[sum DOlor,<br>Sit Amet Usie<br>Services<br>Contact Us</div>
  <div class="footer-mail abs">I was hoping to link up my<br>email on<br><a>fenwickgrading@mailbox-example.net</a><br>with the website if possible.</div>
  <div class="footer-rule abs"></div>
  <div class="copyright abs">Copyright2024@Fenwick Grading LTD. All Rights Reserved</div>
  <div class="footer-social abs"></div>
</footer>

</body>
</html>
```